KAJU Freightways #ALLKAJU Business Cards & Letterhead

I am looking to business cards designed for our organization. We are currently undergoing a small re-branding that is taking place. Our organization is called KAJU Freightways and we are headquartered in Phoenix, AZ. We primarily provide transportation and logistics services to the Marlow Parcel Bureau who is our largest customer. I would like to see a design that incorporates name, title, contact info, website, and address (this will be different depending on the employee). I would also like to see some color on the business card using our logo colors or a variation. I would like our logo on the back of the business card with the website displayed. The final design should communicate that we are a next generation transportation operate that focuses on being driver-first, customer-centric, innovative, and sustainable.We would also like our #ALLKAJU catch phrase incorporated as well.

Target Market(s)

Transportation & Logistics

Industry/Entity Type

Trucking Company

Contact Information for Business Card

-First and Last Name
-Position Title
-Contact Phone
-Contact Email
-Physical Address

Font styles to use
Serif

Colors

Designer to choose colors to be used in the design.

Requirements
Must have
• -KAJU logo prominently displayed
• -#ALLKAJU catch phrase used
• -Some amount of color, design gradient, etc.
• -Logo on the back with website listed (https://www.kajufreightco.example)

```html
<!DOCTYPE html>
<html lang="en">
<head>
<meta charset="UTF-8">
<title>KAJU Freightways Business Card</title>
<link href="https://fonts.googleapis.com/css2?family=Roboto+Slab:wght@400;500;700;900&display=swap" rel="stylesheet">
<style>
  :root {
    --backdrop: #3b3b3b;
    --card: #202021;
    --ink: #ffffff;
    --muted: #d9d9d9;
    --green: #7dc122;
    --teal: #053c4d;
    --ring-dark: #4a4a4c;
    --mark-dark: #3c3c3e;
  }
  * { margin: 0; padding: 0; box-sizing: border-box; }
  html, body {
    width: 799px; height: 1200px; overflow: hidden;
    background: var(--backdrop);
    font-family: 'Roboto Slab', Georgia, serif;
  }
  .sheet { position: relative; width: 799px; height: 1200px; }
  .card {
    position: absolute; left: 50px; width: 700px; height: 400px;
    background: var(--card); overflow: hidden;
    box-shadow: 0 14px 30px rgba(0,0,0,0.45);
  }
  .card--back { top: 95px; }
  .card--front { top: 705px; }

  /* Back */
  .back-mark {
    position: absolute; left: 255px; top: 60px; width: 190px; height: 190px;
    border: 4px solid var(--ring-dark); border-radius: 50%;
    display: flex; align-items: center; justify-content: center;
  }
  .back-mark__name {
    font-weight: 900; font-size: 52px; color: var(--mark-dark); letter-spacing: 1px;
  }
  .back-web {
    position: absolute; left: 0; right: 0; top: 300px;
    display: flex; align-items: center; justify-content: center; gap: 22px;
  }
  .back-web__dash { width: 36px; height: 3px; background: var(--green); }
  .back-web__url { color: var(--ink); font-size: 16px; letter-spacing: 3px; }
  .back-tag {
    position: absolute; left: 0; right: 0; top: 338px; text-align: center;
    color: var(--green); font-size: 15px; font-weight: 700; letter-spacing: 3px;
  }

  /* Front */
  .front-mark {
    position: absolute; left: 55px; top: 45px; width: 200px; height: 200px;
    border: 6px solid var(--green); border-radius: 50%;
    display: flex; align-items: center; justify-content: center;
  }
  .front-mark__name {
    font-weight: 900; font-size: 54px; color: var(--ink); letter-spacing: 1px;
  }
  .person { position: absolute; left: 395px; top: 88px; color: var(--ink); }
  .person__name { font-size: 24px; font-weight: 700; line-height: 30px; }
  .person__title {
    font-size: 16px; color: var(--muted); padding-bottom: 8px;
    border-bottom: 2px solid var(--green); width: 160px;
  }
  .contact { list-style: none; margin-top: 10px; font-size: 15px; }
  .contact li { display: flex; align-items: center; gap: 12px; line-height: 24px; }
  .contact svg { width: 14px; height: 14px; flex: none; }
  .address { font-size: 15px; line-height: 22px; margin-top: 2px; margin-left: -26px; }
  .band-green {
    position: absolute; left: 0; top: 290px; width: 340px; height: 12px;
    background: var(--green);
  }
  .band-teal {
    position: absolute; left: 322px; top: 302px; right: 0; bottom: 0;
    background: var(--teal); border-top-left-radius: 26px;
    display: flex; align-items: center; justify-content: center;
  }
  .band-teal__company { color: var(--ink); font-weight: 700; font-size: 20px; }
</style>
</head>
<body>
<main class="sheet">

  <section class="card card--back">
    <div class="back-mark"><span class="back-mark__name">KAJU</span></div>
    <div class="back-web">
      <span class="back-web__dash"></span>
      <span class="back-web__url">www.kajufreightco.example</span>
      <span class="back-web__dash"></span>
    </div>
    <p class="back-tag">#ALLKAJU</p>
  </section>

  <section class="card card--front">
    <div class="front-mark"><span class="front-mark__name">KAJU</span></div>

    <div class="person">
      <h1 class="person__name">Dorian Halvorsen</h1>
      <p class="person__title">Chairman &amp; CEO</p>
      <ul class="contact">
        <li>
          <svg viewBox="0 0 16 16"><path fill="#7dc122" d="M3 1h3l1.5 4-2 1.3a9 9 0 0 0 4.2 4.2L11 8.5l4 1.5v3a2 2 0 0 1-2 2A12 12 0 0 1 1 3a2 2 0 0 1 2-2z"/></svg>
          480-555-0142
        </li>
        <li>
          <svg viewBox="0 0 16 16"><rect x="1" y="3" width="14" height="10" fill="#7dc122"/><path d="M1 3l7 6 7-6" stroke="#202021" stroke-width="1.5" fill="none"/></svg>
          dorian@kajufreightco.example
        </li>
        <li>
          <svg viewBox="0 0 16 16"><circle cx="8" cy="8" r="7" fill="#7dc122"/><path d="M1 8h14M8 1c-3 3-3 11 0 14M8 1c3 3 3 11 0 14" stroke="#202021" stroke-width="1" fill="none"/></svg>
          www.kajufreightco.example
        </li>
      </ul>
      <p class="address">4410 North Canyon Ridge<br>Road Phoenix, AZ 85021</p>
    </div>

    <div class="band-green"></div>
    <div class="band-teal"><span class="band-teal__company">KAJU Freightways &amp; Energy</span></div>
  </section>

</main>
</body>
</html>
```